Bright Nook Home Page (A Home Wellness e-commerce site & blog)

We need a dynamic home page created for a home wellness brand. Must be visually appealing and extremely mobile-friendly. Logos and a Navmap have been provided but that is just a guideline, PLEASE USE YOUR CREATIVITY.

Target Market(s)

1st target demo: females 24-48, 2nd target demo: all 24-48

Number of Pages Required

1 page

```html
<!DOCTYPE html>
<html lang="en">
<head>
<meta charset="utf-8">
<title>Bright Nook – Home Wellness</title>
<link href="https://fonts.googleapis.com/css2?family=Montserrat:wght@400;500;600&family=Roboto:wght@400;500&display=swap" rel="stylesheet">
<style>
:root{
  --teal:#2fb5bf;
  --purple:#3d1e83;
  --ink:#333333;
  --muted:#666666;
  --line:#e6e6e6;
  --footer:#1f1f1f;
  --white:#ffffff;
  --footer-text:#dddddd;
}
*{box-sizing:border-box;margin:0;padding:0}
html,body{width:1200px;height:3519px;overflow:hidden;background:var(--white)}
.page{position:relative;width:1200px;height:3519px;overflow:hidden;font-family:'Roboto',Arial,sans-serif;color:var(--ink)}
.abs{position:absolute}

/* top bar */
.promo-bar{left:0;top:0;width:1200px;height:52px;background:var(--teal);color:var(--white);font:600 15px 'Montserrat',sans-serif;text-align:center;line-height:54px}

/* header */
.site-header{left:0;top:52px;width:1200px;height:137px;background:var(--white);box-shadow:0 2px 4px rgba(0,0,0,.08);z-index:2}
.brand{font-family:'Montserrat',sans-serif;font-weight:500;white-space:nowrap;letter-spacing:-.5px}
.header-brand{left:112px;top:48px;font-size:44px;color:var(--purple)}
.social-dot{width:38px;height:38px;border-radius:50%;background:var(--teal)}
.main-nav{top:88px;font:500 14px 'Montserrat',sans-serif;color:var(--ink)}
.main-nav.active{color:var(--purple)}
.cart{left:1072px;top:82px}

/* hero */
.hero{left:0;top:189px;width:1200px;height:700px;background:linear-gradient(100deg,#e4ecea 0%,#d9e4df 38%,#c7a98c 62%,#e9d2bd 80%,#d9c4b0 100%)}
.hero-brand{left:75px;top:402px;font-size:66px;color:var(--teal)}
.hero-sub{left:90px;top:510px;width:440px;font:500 24px/34px 'Montserrat',sans-serif;color:var(--ink)}
.btn{display:block;text-align:center;border-radius:40px;font:500 16px 'Montserrat',sans-serif;color:var(--white)}
.btn-shop{left:90px;top:603px;width:164px;height:60px;line-height:60px;background:var(--purple)}
.hero-curve{left:0;top:820px;z-index:1}
.sale-box{left:179px;top:845px;width:842px;height:168px;background:var(--teal);border-radius:40px;color:var(--white);text-align:center;font:500 26px/42px 'Montserrat',sans-serif;padding-top:43px;z-index:2}

/* section headings */
.eyebrow{left:0;width:1200px;text-align:center;font:600 21px 'Montserrat',sans-serif;color:var(--teal)}
.section-title{left:0;width:1200px;text-align:center;font:400 26px/37px 'Montserrat',sans-serif;color:var(--ink)}

/* product grid */
.tile{position:absolute}
.featured-card{left:437px;top:1235px;width:326px;height:462px;background:linear-gradient(160deg,#3aa3c9 0%,#3f7fbf 45%,#4a3c9e 100%);color:var(--white);text-align:center}
.featured-card .stars{position:absolute;top:290px;width:100%;font-size:16px;letter-spacing:3px}
.featured-card .pname{position:absolute;top:322px;width:100%;font:500 22px 'Montserrat',sans-serif}
.featured-card .price{position:absolute;top:355px;width:100%;font:500 28px 'Montserrat',sans-serif}

/* about */
.about{left:0;top:1981px;width:1200px;height:487px;background:linear-gradient(90deg,#d8d6d3 0%,#eae8e6 40%,#f3f2f1 60%,#f5f4f3 100%)}
.about-title{left:677px;top:2045px;font:500 42px 'Montserrat',sans-serif;color:var(--ink)}
.about-rule{left:677px;top:2108px;width:46px;height:3px;background:var(--teal)}
.about-text{left:677px;top:2140px;width:395px;font:14.5px/27.5px Arial,sans-serif;color:#555}
.btn-more{left:677px;top:2330px;width:169px;height:60px;line-height:60px;background:var(--teal)}

/* blog */
.blog-img{position:absolute;top:2652px;width:315px;height:228px}
.blog-card{position:absolute;top:2864px;width:284px;height:224px;background:var(--white);box-shadow:0 1px 6px rgba(0,0,0,.12);text-align:center}
.blog-card .date{margin-top:26px;font:600 17px 'Montserrat',sans-serif;color:var(--teal)}
.blog-card .title{margin-top:12px;font:600 15px/26px 'Montserrat',sans-serif;color:#444}
.blog-card .excerpt{margin:10px auto 0;width:240px;font:13px/26px Arial,sans-serif;color:#666}

/* footer */
.site-footer{color:var(--white)}
.footer{left:0;top:3156px;width:1200px;height:363px;background:var(--footer)}
.footer-brand{left:112px;top:3248px;font-size:44px;color:var(--white)}
.foot-social{width:36px;height:36px;border:2px solid var(--white);border-radius:50%;top:3326px}
.foot-head{top:3195px;font:500 17px 'Montserrat',sans-serif;letter-spacing:.5px;color:var(--white)}
.foot-link{left:418px;font:14px Arial,sans-serif;color:var(--footer-text)}
.foot-link span{display:inline-block;width:32px}
.contact-icon{left:607px;width:36px;height:36px;border-radius:50%;background:#333}
.contact-text{left:655px;font:13px/24px Arial,sans-serif;color:var(--footer-text)}
.news-text{left:872px;top:3240px;width:225px;font:13px/21px Arial,sans-serif;color:var(--footer-text)}
.email-field{left:874px;top:3299px;width:215px;height:39px;background:var(--white);color:#888;font:12px Arial,sans-serif;padding:13px 14px}
.submit{left:874px;top:3351px;width:84px;height:30px;background:var(--teal);font:600 12px/30px 'Montserrat',sans-serif;text-align:center;color:var(--white)}
.copyright{left:0;top:3468px;width:1200px;text-align:center;font:15px Arial,sans-serif;color:var(--footer-text)}
.live-chat{left:1149px;top:3267px;width:51px;height:183px;background:var(--teal);border-radius:6px 0 0 6px}
.live-chat span{position:absolute;left:14px;top:150px;transform-origin:0 0;transform:rotate(-90deg);white-space:nowrap;font:500 16px 'Montserrat',sans-serif;color:var(--white);letter-spacing:1px}
</style>
</head>
<body>
<div class="page">

  <div class="abs promo-bar">FREE SHIPPING ON ALL ORDERS $50 AND OVER!</div>

  <header class="abs site-header">
    <div class="abs brand header-brand">Bright Nook</div>
    <div class="abs social-dot" style="left:964px;top:22px"></div>
    <div class="abs social-dot" style="left:1006px;top:22px"></div>
    <div class="abs social-dot" style="left:1050px;top:22px"></div>
    <nav>
      <div class="abs main-nav active" style="left:560px">HOME</div>
      <div class="abs main-nav" style="left:646px">ABOUT US</div>
      <div class="abs main-nav" style="left:762px">PRODUCT</div>
      <div class="abs main-nav" style="left:875px">BLOG</div>
      <div class="abs main-nav" style="left:958px">CONTACT US</div>
    </nav>
    <div class="abs" style="left:1062px;top:86px;width:1px;height:20px;background:#bbb"></div>
    <svg class="abs cart" width="20" height="26" viewBox="0 0 20 26" aria-label="Cart">
      <text x="7" y="7" font-size="9" fill="#2fb5bf" font-family="Arial">0</text>
      <path d="M1 10h3l2 9h10l2-7H5" fill="none" stroke="#2fb5bf" stroke-width="2"/>
      <circle cx="8" cy="23" r="1.8" fill="#2fb5bf"/><circle cx="15" cy="23" r="1.8" fill="#2fb5bf"/>
    </svg>
  </header>

  <section>
    <div class="abs hero" role="img" aria-label="Photo of a smiling woman with a towel on her head applying face cream"></div>
    <div class="abs brand hero-brand">Bright Nook</div>
    <p class="abs hero-sub">Sed ut perspiciatis unde omnis iste natus error sit voluptatem</p>
    <a class="abs btn btn-shop">SHOP NOW</a>
    <svg class="abs hero-curve" width="1200" height="80" viewBox="0 0 1200 80">
      <path d="M0 20 Q600 110 1200 22 L1200 80 L0 80Z" fill="#fff"/>
      <path d="M0 20 Q600 110 1200 22" fill="none" stroke="#2fb5bf" stroke-width="3"/>
    </svg>
    <div class="abs sale-box">50% OFF SALE GOING ON NOW!<br>BECAUSE SAVING MONEY ALSO MAKES US HAPPY</div>
  </section>

  <section>
    <h2 class="abs eyebrow" style="top:1072px">FEATURED PRODUCT</h2>
    <p class="abs section-title" style="top:1107px">THE KEY TO TOTAL BLISS IS NURTURING<br>THE MIND, BODY, AND SOUL</p>

    <div class="tile" style="left:112px;top:1235px;width:315px;height:226px;background:linear-gradient(135deg,#d9dcd6,#6cbcb8 50%,#8a6a44)" role="img" aria-label="Photo of rolled teal towels, candles and plants"></div>
    <div class="tile" style="left:773px;top:1235px;width:316px;height:226px;background:linear-gradient(135deg,#e8ede0,#6f9a3c 45%,#b08c64)" role="img" aria-label="Photo of a wellness tag among white flowers"></div>
    <div class="tile" style="left:112px;top:1471px;width:315px;height:226px;background:linear-gradient(135deg,#6b5440,#e0a24c 50%,#3a2a1f)" role="img" aria-label="Photo of lit candles and spa stones"></div>
    <div class="tile" style="left:773px;top:1471px;width:316px;height:226px;background:linear-gradient(135deg,#5a3c24,#d8c09a 45%,#7f9a4c)" role="img" aria-label="Photo of natural soaps, scrubs and lemons"></div>
    <div class="tile featured-card" role="img" aria-label="Featured product over a photo of a woman relaxing at a spa">
      <div class="stars">★★★★★</div>
      <div class="pname">PRODUCT NAME</div>
      <div class="price">$25.00</div>
    </div>
    <div class="tile" style="left:112px;top:1706px;width:482px;height:189px;background:linear-gradient(180deg,#9bb06a,#e6e2da 50%,#c8a882)" role="img" aria-label="Photo of wooden blocks spelling wellness under palm leaves"></div>
    <div class="tile" style="left:606px;top:1706px;width:482px;height:189px;background:linear-gradient(90deg,#f2f0ec,#d7b27a 50%,#eeece8 75%,#7f9a5a)" role="img" aria-label="Photo of a candle and skincare bottles"></div>
  </section>

  <section>
    <div class="abs about" role="img" aria-label="Photo of a woman meditating in a cross-legged yoga pose"></div>
    <h2 class="abs about-title">ABOUT US</h2>
    <div class="abs about-rule"></div>
    <p class="abs about-text">They say that home is where the heart is. But home is also where your mind and body reside. At Bright Nook we bel ieve that home should be your place of Zen. A respite from the crazy world outside those walls. It is where you recharge your soul so you can approach each day with the focus and energy necessary to conquer the world.</p>
    <a class="abs btn btn-more">TELL ME MORE</a>
  </section>

  <section>
    <h2 class="abs eyebrow" style="top:2511px">THE BRIGHT BLOG</h2>
    <p class="abs section-title" style="top:2547px">FOOD FOR THE MIND, TIPS FOR THE BODY AND<br>EXERCISES FOR THE SOUL</p>

    <div class="blog-img" style="left:112px;background:linear-gradient(135deg,#8a5a3c,#c9b8a2 50%,#5e8e8a)" role="img" aria-label="Photo of a woman stretching on a yoga mat"></div>
    <div class="blog-img" style="left:444px;background:linear-gradient(135deg,#ece6de,#b9a796 50%,#efe9e1)" role="img" aria-label="Photo of a group meditating in a yoga class"></div>
    <div class="blog-img" style="left:774px;background:linear-gradient(135deg,#3a2a1e,#c6a04a 50%,#5a3e2a)" role="img" aria-label="Photo of essential oils, flowers and spa stones"></div>

    <article class="blog-card" style="left:128px">
      <div class="date">03 MAY 2021</div>
      <div class="title">SED UT PERSPICIATIS UNDE<br>OMNIS ISTE NATUS</div>
      <p class="excerpt">Nemo enim ipsam voluptatem quia vol uptas sit aspernatur aut odit aut fugit, eos qui ratione voluptatem</p>
    </article>
    <article class="blog-card" style="left:459px">
      <div class="date">03 MAY 2021</div>
      <div class="title">SED UT PERSPICIATIS UNDE<br>OMNIS ISTE NATUS</div>
      <p class="excerpt">Nemo enim ipsam voluptatem quia vol uptas sit aspernatur aut odit aut fugit, eos qui ratione voluptatem</p>
    </article>
    <article class="blog-card" style="left:790px">
      <div class="date">03 MAY 2021</div>
      <div class="title">SED UT PERSPICIATIS UNDE<br>OMNIS ISTE NATUS</div>
      <p class="excerpt">Nemo enim ipsam voluptatem quia vol uptas sit aspernatur aut odit aut fugit, eos qui ratione voluptatem</p>
    </article>
  </section>

  <footer class="site-footer">
    <div class="abs footer"></div>
    <div class="abs brand footer-brand">Bright Nook</div>
    <div class="abs foot-social" style="left:147px"></div>
    <div class="abs foot-social" style="left:190px"></div>
    <div class="abs foot-social" style="left:233px"></div>
    <div class="abs foot-social" style="left:276px"></div>
    <div class="abs foot-social" style="left:319px"></div>

    <div class="abs foot-head" style="left:418px">QUICK LINKS</div>
    <div class="abs foot-link" style="top:3241px"><span>→</span>HOME</div>
    <div class="abs foot-link" style="top:3268px"><span>→</span>ABOUT US</div>
    <div class="abs foot-link" style="top:3295px"><span>→</span>PRODUCT</div>
    <div class="abs foot-link" style="top:3322px"><span>→</span>BLOG</div>
    <div class="abs foot-link" style="top:3350px"><span>→</span>CONTACT US</div>

    <div class="abs foot-head" style="left:612px">CONTACT</div>
    <svg class="abs contact-icon" style="top:3239px" viewBox="0 0 36 36" aria-label="Phone"><path d="M13 11l3 0 1 4-2 1a9 9 0 0 0 5 5l1-2 4 1 0 3c-7 1-13-5-12-12z" fill="#fff"/></svg>
    <div class="abs contact-text" style="top:3245px">000 -555- 0147</div>
    <svg class="abs contact-icon" style="top:3287px" viewBox="0 0 36 36" aria-label="Email"><rect x="11" y="13" width="14" height="10" fill="none" stroke="#fff" stroke-width="1.5"/><path d="M11 13l7 6 7-6" fill="none" stroke="#fff" stroke-width="1.5"/></svg>
    <div class="abs contact-text" style="top:3293px">info@yourbrightnook.com</div>
    <svg class="abs contact-icon" style="top:3337px" viewBox="0 0 36 36" aria-label="Location"><path d="M18 10a5 5 0 0 1 5 5c0 4-5 10-5 10s-5-6-5-10a5 5 0 0 1 5-5z" fill="#fff"/><circle cx="18" cy="15" r="2" fill="#333"/></svg>
    <div class="abs contact-text" style="top:3337px">#154 lore Ipsum dummy<br>Loram ipsum</div>

    <div class="abs foot-head" style="left:872px">NEWSLETTER</div>
    <p class="abs news-text">Sed ut perspiciatis unde omnis us error sit voluptatem</p>
    <div class="abs email-field">Email :</div>
    <div class="abs submit">SUBMIT</div>

    <div class="abs copyright">© Copyrights 2021 Bright Nook.All Rights Reserved.</div>
    <div class="abs live-chat"><span>LIVE CHAT</span></div>
  </footer>

</div>
</body>
</html>
```